4th Generation Family Business Needs a New Card Design!

We are a family owned 4th Generation company. We are based in the Sydney, Australia area and we are desperately in need of a more modern and classy card. We are monumental masons who design, supply & erect lasting memorials throughout cemeteries in Sydney. Our customers are normally in a period of grieving. I have attached logo files that will need to be implemented on the card. Company was established 1935. Australian Owned and Operated. Card needs to be designed to PIXO.com specification.

Target Market(s)

Our target market is based upon people that a grieving for family members that have passed away. We also deal with alot of companies that own and operate cemeteries.

Industry/Entity Type

Business

Contact Information for Business Card

Simon Harcourt, Operations Manager, 0417293086, simon@harcourtmemorials.com.au
Lewis Harcourt, Director, 0491630572, lewis@harcourtmemorials.com.au
Phone # 02 9561 3048
Website: www.harcourtmemorials.com.au
Address: Suite 17, 8 Palfrey Lane, West Carlow, Sydney NSW 2156

Font styles to use
Serif
Decorative
Script

Requirements
Must have
• Would like to see the logo nicely implemented with a modern design. Embossed lettering would be a nice additive.

```html
<!DOCTYPE html>
<html lang="en">
<head>
<meta charset="utf-8">
<title>Harcourt Memorials – Business Card</title>
<link href="https://fonts.googleapis.com/css2?family=Montserrat:wght@400;500;600&display=swap" rel="stylesheet">
<style>
  :root {
    --backdrop: #2b2b2d;
    --card-black: #050505;
    --card-white: #ffffff;
    --gold: #e8b820;
    --ink: #111111;
    --paper-text: #f4f4f4;
    --divider: #3a3a3a;
  }
  * { box-sizing: border-box; margin: 0; padding: 0; }
  html, body { width: 1200px; height: 900px; overflow: hidden; }
  body {
    background: var(--backdrop);
    font-family: "Montserrat", sans-serif;
    display: flex;
    flex-direction: column;
    align-items: center;
    justify-content: center;
    gap: 40px;
  }
  .card {
    width: 620px;
    height: 380px;
    border-radius: 22px;
    position: relative;
    overflow: hidden;
    box-shadow: 0 14px 30px rgba(0,0,0,.45);
  }

  /* Front */
  .card-front {
    background: var(--card-black);
    color: var(--paper-text);
    display: flex;
    flex-direction: column;
    align-items: center;
    justify-content: center;
  }
  .brand {
    display: flex;
    align-items: center;
    gap: 14px;
  }
  .brand-square {
    width: 26px;
    height: 26px;
    background: var(--gold);
  }
  .brand-name {
    font-weight: 500;
    letter-spacing: 3px;
    text-transform: uppercase;
  }
  .card-front .brand-name { font-size: 34px; color: var(--paper-text); }
  .front-rule {
    width: 300px;
    height: 2px;
    background: var(--gold);
    margin-top: 18px;
  }
  .front-web {
    position: absolute;
    bottom: 48px;
    font-size: 17px;
    letter-spacing: .5px;
  }
  .front-web .accent { color: var(--gold); font-weight: 600; }

  /* Back */
  .card-back {
    background: var(--card-white);
    color: var(--ink);
    display: flex;
    align-items: center;
  }
  .back-brand {
    width: 290px;
    display: flex;
    justify-content: center;
  }
  .card-back .brand-name { font-size: 22px; color: var(--ink); letter-spacing: 2px; }
  .card-back .brand-square { width: 20px; height: 20px; }
  .back-divider {
    width: 2px;
    height: 200px;
    background: linear-gradient(to bottom, transparent, var(--divider) 20%, var(--divider) 80%, transparent);
  }
  .contact {
    padding-left: 28px;
    font-size: 14.5px;
    line-height: 1.45;
  }
  .contact-name {
    font-size: 24px;
    font-weight: 600;
    color: var(--gold);
    line-height: 1.1;
  }
  .contact-title { margin-bottom: 4px; }
  .contact-line {
    display: flex;
    align-items: center;
    gap: 8px;
  }
  .contact-line svg { width: 12px; height: 12px; flex: none; }
  .contact-line .accent { color: var(--gold); }
</style>
</head>
<body>

  <section class="card card-front">
    <div class="brand">
      <span class="brand-square"></span>
      <span class="brand-name">Harcourt Memorials</span>
    </div>
    <div class="front-rule"></div>
    <p class="front-web">www.<span class="accent">harcourtmemorials</span>.com.au</p>
  </section>

  <section class="card card-back">
    <div class="back-brand">
      <div class="brand">
        <span class="brand-square"></span>
        <span class="brand-name">Harcourt Memorials</span>
      </div>
    </div>
    <div class="back-divider"></div>
    <div class="contact">
      <p class="contact-name">Lewis Harcourt</p>
      <p class="contact-title">Director</p>
      <p>Suite 17, 8 Palfrey Lane</p>
      <p>West Carlow, Sydney NSW 2156</p>
      <p class="contact-line">
        <svg viewBox="0 0 12 12"><rect x="3" y="1" width="6" height="10" rx="1" fill="none" stroke="#e8b820" stroke-width="1.3"/></svg>
        0491630572
      </p>
      <p class="contact-line">
        <svg viewBox="0 0 12 12"><path d="M2 1.5 L4.5 1.5 L5 4 L3.8 5 Q5 7.5 7 8.2 L8 7 L10.5 7.5 L10.5 10 Q5 10.5 1.5 4 Z" fill="#e8b820"/></svg>
        02 9561 3048
      </p>
      <p class="contact-line">
        <svg viewBox="0 0 12 12"><rect x="1" y="2.5" width="10" height="7" fill="none" stroke="#e8b820" stroke-width="1.2"/><path d="M1 2.5 L6 6.5 L11 2.5" fill="none" stroke="#e8b820" stroke-width="1.2"/></svg>
        lewis@harcourtmemorials.com.au
      </p>
      <p class="contact-line">
        <svg viewBox="0 0 12 12"><circle cx="6" cy="6" r="5" fill="none" stroke="#e8b820" stroke-width="1.2"/><ellipse cx="6" cy="6" rx="2.2" ry="5" fill="none" stroke="#e8b820" stroke-width="1"/><path d="M1 6 H11" stroke="#e8b820" stroke-width="1"/></svg>
        <span>www.<span class="accent">harcourtmemorials</span>.com.au</span>
      </p>
    </div>
  </section>

</body>
</html>
```